Heron Haulage needs Bussiness cards!

Our new trucking company needs business cards!
We need the same design with two different names and emails, everything else it's the same.
I have included our original logo so we can use it for the design.
Note: the logo to be used is the o e with the buffalo on the right side, next to the letters H and H.

Target Market(s)

Trucking, refrigerated transportation, freight

Industry/Entity Type

Business

Contact Information for Business Card

Card #1:
Marcus Whitfield
marcuswhitfield@heronhaulage.example
1-855-317-6094
(956)238-7160
4117 W. Larkin Ave.
Pharr, TX 78590
www.heronhaulage.example

Card#2:
Rosalba Quintero
rosalba@heronhaulage.example
1-855-317-6094
(956)238-7160
4117 W. Larkin Ave.
Pharr, TX 78590
www.heronhaulage.example

Font styles to use
Sans Serif

Colors
0655a3
ec1f27
ffffff

Requirements
Must have
• our logo
Nice to have
• roads on background,

```html
<!DOCTYPE html>
<html lang="en">
<head>
<meta charset="utf-8">
<title>Heron Haulage – Business Cards</title>
<link rel="stylesheet" href="https://fonts.googleapis.com/css2?family=Lato:wght@400;700;900&display=swap">
<style>
  :root {
    --brand-blue: #0655a3;
    --brand-red: #ec1f27;
    --paper: #ffffff;
    --ink: #3a3a3a;
    --backdrop: #e9e6e2;
  }
  * { margin: 0; padding: 0; box-sizing: border-box; }
  html, body { width: 1200px; height: 848px; overflow: hidden; }
  body {
    background: var(--backdrop);
    font-family: "Lato", Arial, sans-serif;
    position: relative;
  }
  .card {
    position: absolute;
    box-shadow: 0 3px 8px rgba(0,0,0,.25);
    overflow: hidden;
  }
  .card-front {
    width: 548px; height: 291px; top: 110px;
    background: var(--brand-blue);
  }
  .card-front.left { left: 27px; }
  .card-front.right { left: 626px; }
  .front-wordmark {
    position: absolute; left: 0; right: 0; top: 128px;
    text-align: center;
    color: var(--paper);
    font-weight: 900; font-size: 46px; letter-spacing: .5px;
  }
  .front-url {
    position: absolute; left: 0; right: 0; top: 249px;
    text-align: center; color: var(--paper);
    font-weight: 700; font-size: 12px;
  }
  .front-url .accent { color: var(--brand-red); }

  .card-back {
    width: 548px; height: 294px; top: 476px;
    background: var(--paper);
  }
  .card-back.left { left: 27px; }
  .card-back.right { left: 626px; width: 547px; }
  .back-wordmark {
    position: absolute; left: 35px; top: 38px;
    color: var(--brand-blue);
    font-weight: 900; font-size: 36px;
  }
  .card-back.right .back-wordmark { top: 34px; font-size: 34px; }
  .brand-decoration {
    position: absolute; left: 35px; top: 100px; width: 510px; height: 170px;
    background: radial-gradient(ellipse at 25% 55%, rgba(6,85,163,.10), rgba(236,31,39,.05) 45%, transparent 70%);
  }
  .holder-name {
    position: absolute; left: 35px; top: 143px;
    color: var(--brand-red); font-size: 16px;
  }
  .card-back.right .holder-name {
    top: 152px; color: var(--brand-blue); font-size: 20px; letter-spacing: .3px;
  }
  .holder-title {
    position: absolute; left: 35px; top: 163px;
    color: var(--ink); font-size: 12px;
  }
  .name-rule {
    position: absolute; left: 35px; height: 1px; background: var(--brand-red);
    top: 178px; width: 476px;
  }
  .card-back.right .name-rule { top: 179px; width: 475px; }
  .contact-list { position: absolute; left: 35px; list-style: none; }
  .card-back.left .contact-list { top: 202px; }
  .card-back.right .contact-list { top: 197px; }
  .contact-list li {
    display: flex; align-items: center; gap: 5px;
    height: 16.5px; color: var(--ink); font-size: 12px;
  }
  .contact-list svg { width: 11px; height: 11px; flex: none; }
  .card-back.left .contact-list svg { color: var(--brand-blue); }
  .card-back.right .contact-list svg { color: var(--brand-red); }
  .postal-address {
    position: absolute; right: 37px; text-align: right;
    font-style: normal; color: var(--ink); font-size: 12px; line-height: 18px;
  }
  .card-back.left .postal-address { top: 234px; }
  .card-back.right .postal-address { top: 229px; }
  .footer-band {
    position: absolute; left: 0; right: 0; bottom: 0; height: 15px;
    display: flex; gap: 3px;
  }
  .footer-band .blue { width: 273px; background: var(--brand-blue); }
  .footer-band .red { flex: 1; background: var(--brand-red); }
</style>
</head>
<body>
<svg width="0" height="0" style="position:absolute" aria-hidden="true">
  <defs>
    <symbol id="icon-phone" viewBox="0 0 24 24"><path fill="currentColor" d="M6.6 10.8a15.1 15.1 0 0 0 6.6 6.6l2.2-2.2c.3-.3.7-.4 1-.2 1.1.4 2.3.6 3.6.6.6 0 1 .4 1 1V20c0 .6-.4 1-1 1A17 17 0 0 1 3 4c0-.6.4-1 1-1h3.5c.6 0 1 .4 1 1 0 1.3.2 2.5.6 3.6.1.3 0 .7-.2 1z"/></symbol>
    <symbol id="icon-mobile" viewBox="0 0 24 24"><rect x="6" y="2" width="12" height="20" rx="2" fill="none" stroke="currentColor" stroke-width="2.4"/><circle cx="12" cy="18" r="1.3" fill="currentColor"/></symbol>
    <symbol id="icon-mail" viewBox="0 0 24 24"><rect x="2" y="5" width="20" height="14" rx="1.5" fill="currentColor"/><path d="M3 6l9 7 9-7" fill="none" stroke="#fff" stroke-width="1.6"/></symbol>
    <symbol id="icon-globe" viewBox="0 0 24 24"><circle cx="12" cy="12" r="10" fill="currentColor"/><path d="M2 12h20M12 2c3 3 3 17 0 20M12 2c-3 3-3 17 0 20" fill="none" stroke="#fff" stroke-width="1.3"/></symbol>
  </defs>
</svg>

<section class="card card-front left">
  <div class="front-wordmark">Heron Haulage</div>
  <div class="front-url">www.<span class="accent">heronhaulage</span>.example</div>
</section>

<section class="card card-front right">
  <div class="front-wordmark">Heron Haulage</div>
  <div class="front-url">www.<span class="accent">heronhaulage</span>.example</div>
</section>

<section class="card card-back left">
  <div class="brand-decoration" role="img" aria-label="Faint large brand decoration"></div>
  <div class="back-wordmark">Heron Haulage</div>
  <div class="holder-name">Rosalba Quintero</div>
  <div class="holder-title">President</div>
  <div class="name-rule"></div>
  <ul class="contact-list">
    <li><svg><use href="#icon-phone"/></svg>(956)238-7160</li>
    <li><svg><use href="#icon-mobile"/></svg>1-855-317-6094</li>
    <li><svg><use href="#icon-mail"/></svg>rosalba@heronhaulage.example</li>
    <li><svg><use href="#icon-globe"/></svg>www.heronhaulage.example</li>
  </ul>
  <address class="postal-address">4117 W. Larkin Ave.<br>Pharr, TX 78590</address>
  <div class="footer-band"><span class="blue"></span><span class="red"></span></div>
</section>

<section class="card card-back right">
  <div class="brand-decoration" role="img" aria-label="Faint large brand decoration"></div>
  <div class="back-wordmark">Heron Haulage</div>
  <div class="holder-name">Marcus Whitfield</div>
  <div class="name-rule"></div>
  <ul class="contact-list">
    <li><svg><use href="#icon-phone"/></svg>(956)238-7160</li>
    <li><svg><use href="#icon-mobile"/></svg>1-855-317-6094</li>
    <li><svg><use href="#icon-mail"/></svg>marcuswhitfield@heronhaulage.example</li>
    <li><svg><use href="#icon-globe"/></svg>www.heronhaulage.example</li>
  </ul>
  <address class="postal-address">4117 W. Larkin Ave.<br>Pharr, TX 78590</address>
  <div class="footer-band"><span class="blue"></span><span class="red"></span></div>
</section>
</body>
</html>
```